Trabworth Business Cards

We need a business card design for Trabworth Mining.

This is a B2B company that buys and sells large machinery tires within the coal mining industry. The design should the strong, crisp and masculine. I have uploaded the company logo and rough mock-up of what the back of the card should look like. the front of the card should have the same look/feel as the back. I need editable templates for both the front and the back of the card.

Color scheme should be grey/green/black

Contact information to include on the card:
Name: Dale Pembrose
Title: Managing Director
Phone: 555-314-2069
Address: 1187 Welford #3 Dallas, TX 75290
Email: Dale@Trabworth-example.com

I am also opening a contest for letterhead design. If you submit a business card design, please also submit a letterhead design with the same look/feel. The winner of the business card design will also will the letter head and be paid for both.

Target Market(s)

Procurement men/women in the coal mining industry

Industry/Entity Type

Coal Mining

```html
<!DOCTYPE html>
<html lang="en">
<head>
<meta charset="utf-8">
<title>Trabworth Mining Business Cards</title>
<link rel="stylesheet" href="https://fonts.googleapis.com/css2?family=Exo+2:wght@700&family=Open+Sans:wght@400;600&display=swap">
<style>
  :root {
    --ink: #050505;
    --green: #6cb83f;
    --white: #ffffff;
    --grey: #b9bcbf;
    --stage: #e6e6e4;
  }
  * { margin: 0; padding: 0; box-sizing: border-box; }
  html, body { width: 1200px; height: 1024px; overflow: hidden; background: var(--stage); }
  .canvas { position: relative; width: 1200px; height: 1024px; }

  .card { position: absolute; background: var(--ink); overflow: hidden; box-shadow: 0 10px 28px rgba(0,0,0,.25); }

  /* Front: landscape */
  .card--front { left: 50px; top: 330px; width: 640px; height: 366px; }
  .front-band { position: absolute; left: 0; top: 0; width: 100%; height: 30px; background: var(--green); }
  .front-rule { position: absolute; left: 0; top: 38px; width: 100%; height: 3px; background: var(--grey); }
  .brand { position: absolute; display: flex; align-items: center; gap: 12px; }
  .brand__square { width: 26px; height: 26px; background: var(--green); flex: none; }
  .brand__name { font-family: "Exo 2", sans-serif; font-weight: 700; color: var(--white); letter-spacing: 2px; text-transform: uppercase; white-space: nowrap; }
  .card--front .brand { left: 44px; top: 82px; }
  .card--front .brand__name { font-size: 34px; }

  .person { position: absolute; left: 44px; top: 168px; font-family: "Open Sans", sans-serif; }
  .person__name { color: var(--white); font-size: 24px; font-weight: 600; line-height: 1.2; }
  .person__title { color: var(--green); font-size: 17px; line-height: 1.4; }
  .contact { margin-top: 20px; list-style: none; font-size: 15px; line-height: 1.65; color: var(--white); }
  .contact__label { color: var(--green); margin-right: 4px; }

  /* Back: portrait */
  .card--back { left: 790px; top: 190px; width: 366px; height: 640px; }
  .card--back .brand { left: 34px; top: 48px; }
  .card--back .brand__square { width: 20px; height: 20px; }
  .card--back .brand__name { font-size: 24px; }
  .back-band { position: absolute; left: 0; top: 255px; width: 100%; height: 64px; background: var(--green); }
</style>
</head>
<body>
<main class="canvas">
  <section class="card card--front" aria-label="Business card front">
    <div class="front-band"></div>
    <div class="front-rule"></div>
    <div class="brand">
      <span class="brand__square"></span>
      <span class="brand__name">Trabworth Mining</span>
    </div>
    <div class="person">
      <p class="person__name">Dale Pembrose</p>
      <p class="person__title">Managing Director</p>
      <ul class="contact">
        <li><span class="contact__label">P:</span>555-314-2069</li>
        <li><span class="contact__label">A:</span>1187 Welford #3 Dallas, TX 75290</li>
        <li><span class="contact__label">E:</span>Dale@Trabworth-example.com</li>
      </ul>
    </div>
  </section>

  <section class="card card--back" aria-label="Business card back">
    <div class="brand">
      <span class="brand__square"></span>
      <span class="brand__name">Trabworth Mining</span>
    </div>
    <div class="back-band"></div>
  </section>
</main>
</body>
</html>
```